Photojournalism/photography business needs a simple, timeless & professional letterhead design

We need a letterhead design for photography/photojournalism business called 'plunq', no capitals.

The letterhead needs to be:
- simple
- professional
- timeless
- easy to read
- consists of at least 2 colors to make it stands out.

We do mainly editorial photography, photo articles for various publications, travel, businesses, as well as people such as family and kids.

The final design should communicate professionalism, easy identification, attention grabbing, even if it has to be found among a stack of various papers on the clients' desks.

Target Market(s)

Various publications.

Industry/Entity Type

Business

Requirements
Must have
• Please use the logo attached.

```html
<!DOCTYPE html>
<html lang="en">
<head>
<meta charset="utf-8">
<title>plunq letterhead</title>
<link href="https://fonts.googleapis.com/css2?family=Source+Sans+3:wght@400;600;800&family=Marck+Script&display=swap" rel="stylesheet">
<style>
  :root {
    --brand-red: #e51f2c;
    --ink: #3a3a3a;
    --ink-soft: #5c5c5c;
    --paper: #ffffff;
    --backdrop: #e9e6e1;
  }
  * { box-sizing: border-box; margin: 0; padding: 0; }
  html, body {
    width: 1200px; height: 1024px; overflow: hidden;
    background: var(--backdrop);
    font-family: "Source Sans 3", Arial, sans-serif;
    color: var(--ink);
  }
  .letterhead {
    position: absolute; left: 250px; top: 18px;
    width: 700px; height: 988px;
    background: var(--paper);
    box-shadow: 0 6px 24px rgba(0,0,0,.18);
  }
  .brand {
    position: absolute; right: 70px; top: 58px;
    display: flex; align-items: center; gap: 10px;
  }
  .brand-mark { width: 20px; height: 20px; background: var(--brand-red); }
  .brand-name {
    font-weight: 800; font-size: 64px; line-height: 1;
    color: var(--brand-red); letter-spacing: -1px;
  }
  .letter-body {
    position: absolute; left: 70px; top: 190px; width: 560px;
    font-size: 13px; line-height: 1.45;
  }
  .salutation { font-size: 15px; margin-bottom: 18px; }
  .letter-body p { margin-bottom: 12px; text-align: left; }
  .sign-off { margin-top: 30px; }
  .signature {
    font-family: "Marck Script", cursive;
    font-size: 28px; color: var(--ink-soft);
  }
  .role { font-size: 14px; color: var(--ink-soft); }
  .contact-line {
    position: absolute; left: 70px; right: 40px; bottom: 78px;
    display: flex; align-items: center; gap: 14px;
    font-size: 12.5px; color: var(--ink-soft); white-space: nowrap;
  }
  .contact-item { display: flex; align-items: center; gap: 5px; }
  .contact-item svg { width: 11px; height: 11px; fill: var(--brand-red); }
  .footer-band {
    position: absolute; left: 0; right: 0; bottom: 0; height: 56px;
    background: var(--brand-red);
    display: flex; align-items: center; justify-content: center;
    color: var(--paper); font-size: 14px; letter-spacing: .3px;
  }
</style>
</head>
<body>
<main class="letterhead">
  <header class="brand">
    <span class="brand-mark"></span>
    <span class="brand-name">plunq</span>
  </header>

  <section class="letter-body">
    <p class="salutation">Lorem Ipsum,</p>
    <p>Duis sit amet dolor sit amet dolor tempor iaculis ac nec ante. Proin nunc diam, egestas eu semper a, fermentum ac leo. Fusce sit amet tempor elit. Mauris auctor interdum massa vitae cursus. Ut adipiscing pellentesque nunc, eget tincidunt magna imperdiet non. Curabitur eleifend elementum nisl eget iaculis. Suspendisse scelerisque ligula a nunc faucibus sit amet elementum dolor dictum.</p>
    <p>Praesent condimentum mi at ultrices fermentum, ipsum lectus consequat mauris, ut vulputate nibh erat id eros. Vivamus ornare mattis libero at dictum. Praesent sodales metus sed nulla laoreet mollis. Curabitur non turpis in orci dignissim gravida. Aliquam tristique mauris a nibh vestibulum sagittis.</p>
    <p>Duis porta semper nibh, tincidunt aliquam metus euismod eget. Morbi varius varius pellentesque. Donec aliquam vulputate tortor non hendrerit. Suspendisse at ipsum ante. Interdum porttitor ligula. Curabitur eu molestie sapien. Sed magna purus, faucibus quis pulvinar nec, commodo vel justo. Nam faucibus ornare varius. Vivamus sit amet felis vitae justo scelerisque malesuada. Etiam venenatis vehicula magna, a eleifend lorem ornare nec. Maecenas eu nisl vel nunc aliquet malesuada vel in lacus.</p>
    <p>Morbi et odio eu ante pharetra iaculis vitae eget arcu. Maecenas gravida, dui vel ultricies aliquet, dui arcu luctus ante, non dignissim ipsum tortor vel orci, um fringilla mi. Mauris porta feugiat nibh et fermentum. Donec scelerisque consequat lacinia.</p>
    <p>Curabitur ac diam ut quam ultrices laoreet at ut tellus. Maecenas vitae urna in lorem condimentum sollicitudin eget vel lacus. Ut nisl turpis, tristique ullamcorper laoreet nec, gravida nec est. Donec elementum malesuada volutpat, in ac arcu quis augue vehicula fringilla.</p>
    <div class="sign-off">
      <div class="signature">Yours name</div>
      <div class="role">Company Director</div>
    </div>
  </section>

  <div class="contact-line">
    <span class="contact-item">Your Address Goes here, City, Zip code, State</span>
    <span class="contact-item">
      <svg viewBox="0 0 24 24"><path d="M6.6 10.8a15 15 0 0 0 6.6 6.6l2.2-2.2a1 1 0 0 1 1-.25 11.4 11.4 0 0 0 3.6.57 1 1 0 0 1 1 1V20a1 1 0 0 1-1 1A17 17 0 0 1 3 4a1 1 0 0 1 1-1h3.5a1 1 0 0 1 1 1c0 1.25.2 2.45.57 3.57a1 1 0 0 1-.25 1z"/></svg>
      000-000-0000
    </span>
    <span class="contact-item">
      <svg viewBox="0 0 24 24"><path d="M6 3h9l3 3v4H6zM3 11h18v8h-3v2H6v-2H3zM8 16v3h8v-3z"/></svg>
      000-000-0000
    </span>
    <span class="contact-item">
      <svg viewBox="0 0 24 24"><path d="M2 5h20v14H2zm2 2v.5l8 5 8-5V7z"/></svg>
      name@domainname.com
    </span>
  </div>

  <footer class="footer-band">www.websitename.com</footer>
</main>
</body>
</html>
```